Intelligent design image for our website

I would like an awesome image for our website that showcases the intelligent design of our app. We currently have a test web site here.
https://www.corvinta.com.au/test-ewd/
I really do not like the graphic next to the "Intelligent design" and i want something much better than this.
Our app is used by Australian Truck Drivers. It would be nice to have a little bit of an Australian feel, but most importantly is should clearly showcase our app look a feel and the screens should be as legible (readable) as possible. These examples could be used for inspiration.
https://pixelmarrow.net/products/free-app-showcase-mockup-psd-5170284
https://www.plonkit.com/community/file/2640519873320957716/PhoneSuite-Landing-Page-Template-for-Mobile-Apps-Showcase

```html
<!DOCTYPE html>
<html lang="en">
<head>
<meta charset="utf-8">
<title>Intelligent design – app screens</title>
<link href="https://fonts.googleapis.com/css2?family=Lato:wght@400;700&display=swap" rel="stylesheet">
<style>
:root{
  --ring:#10a80f;
  --ring-soft:#9fd89f;
  --ink:#1d1d1f;
  --muted:#6b6f76;
  --line:#e3e5ea;
  --brand:#2a9fd8;
  --bar:#3b6ef5;
  --bar-soft:#a6bdf3;
  --alert:#e0584a;
  --panel:#ffffff;
  --tint:#eef3fb;
  --bg:#ffffff;
}
*{box-sizing:border-box;margin:0;padding:0}
html,body{width:1156px;height:1200px;overflow:hidden;background:var(--bg);font-family:"Lato",sans-serif;color:var(--ink)}
.stage{position:relative;width:1156px;height:1200px}
.rings{position:absolute;inset:0}
.screen{position:absolute;top:250px;width:340px;height:700px;background:var(--panel);border-radius:34px;box-shadow:0 18px 50px rgba(0,0,0,.14);overflow:hidden;display:flex;flex-direction:column;font-size:12px}
.screen--left{left:40px;top:300px}
.screen--center{left:408px;top:240px}
.screen--right{left:776px;top:300px}
.status{display:flex;justify-content:space-between;padding:18px 26px 6px;font-weight:700;font-size:15px}
.header{display:flex;align-items:flex-start;gap:12px;padding:10px 18px 12px;border-bottom:1px solid var(--line)}
.menu{width:16px;margin-top:10px}
.menu i{display:block;height:2px;background:var(--ink);margin-bottom:4px}
.who{flex:1}
.who b{display:block;font-size:15px}
.who span{color:var(--muted);font-size:13px}
.sync{display:flex;flex-direction:column;align-items:flex-end;gap:6px}
.sync button{background:var(--brand);color:#fff;border:0;border-radius:3px;padding:4px 9px;font:inherit;font-size:12px}
.body{flex:1;overflow:hidden;padding:10px 14px}
.card{background:#fff;border-radius:8px;box-shadow:0 2px 10px rgba(0,0,0,.08);padding:10px 12px;margin-bottom:12px}
.tab{display:inline-block;background:var(--brand);color:#fff;font-weight:700;padding:5px 16px;border-radius:4px 4px 0 0;font-size:13px}
.band{border-top:3px solid var(--brand);text-align:center;margin-bottom:10px}
.grid2{display:grid;grid-template-columns:1fr 1fr}
.cell{text-align:center;padding:7px 4px;border-bottom:1px solid var(--line)}
.cell:nth-child(odd){border-right:1px solid var(--line)}
.cell b{display:block;font-size:14px}
.cell small{color:var(--muted);font-size:11px;display:block;line-height:1.2}
.navs{display:flex;justify-content:space-between;margin-top:8px}
.pill{border:1px solid var(--brand);color:var(--brand);border-radius:4px;padding:3px 12px;font-size:11px}
.progress{position:relative;height:8px;background:var(--bar-soft);border-radius:4px;margin:8px 0 4px}
.progress i{position:absolute;left:0;top:0;bottom:0;width:55%;background:var(--bar);border-radius:4px}
.range{display:flex;justify-content:space-between;color:var(--muted);font-size:10px}
.period{display:flex;justify-content:space-between;padding:6px 0;border-bottom:1px solid var(--brand)}
.period b{font-size:13px;display:block}
.period small{color:var(--muted);font-size:10px}
.tabbar{display:flex;justify-content:space-around;border-top:1px solid var(--line);padding:10px 4px 22px;font-size:12px}
.tabbar span{display:flex;flex-direction:column;align-items:center;gap:4px}
.days{display:flex;justify-content:space-around;background:#f1f2f4;padding:8px 30px;color:var(--muted);font-size:13px}
.days .on{background:#666;color:#fff;border-radius:50%;width:24px;height:24px;display:grid;place-items:center}
.date{display:block;width:max-content;margin:0 auto 8px;border:1px solid var(--brand);color:var(--brand);padding:3px 8px;border-radius:3px;font-size:14px}
.activity{background:var(--tint);border-radius:6px;padding:10px 12px}
.activity .top{display:flex;justify-content:space-between;border-bottom:1px solid var(--brand);padding-bottom:8px;margin-bottom:8px}
.activity .top b{font-size:14px}
.activity .row{display:flex;justify-content:space-between}
.activity small{color:var(--muted);display:block}
.cal{display:grid;grid-template-columns:repeat(7,1fr);gap:6px;margin:8px 0}
.cal span{width:26px;height:26px;border-radius:50%;display:grid;place-items:center;font-size:10px;border:1.5px solid var(--brand);color:var(--brand)}
.cal .x{border-color:var(--alert);color:var(--alert);background:linear-gradient(135deg,transparent 47%,var(--alert) 48%,var(--alert) 52%,transparent 53%)}
.cal .on{background:var(--brand);color:#fff}
.note{font-size:10px;color:var(--muted);line-height:1.3}
</style>
</head>
<body>
<div class="stage">
  <svg class="rings" width="1156" height="1200" viewBox="0 0 1156 1200" aria-hidden="true">
    <circle cx="566" cy="622" r="497" fill="none" stroke="var(--ring-soft)" stroke-width="7" stroke-dasharray="0 15" stroke-linecap="round"/>
    <circle cx="566" cy="622" r="400" fill="none" stroke="var(--ring)" stroke-width="22"/>
  </svg>

  <!-- Compliance: 14 day rule -->
  <section class="screen screen--left">
    <div class="status"><span>8:48</span><span>●●● ▢</span></div>
    <div class="header">
      <div class="menu"><i></i><i></i><i></i></div>
      <div class="who"><b>Jack Mercer</b><span>License : 1234567890</span></div>
      <div class="sync"><svg width="14" height="14" viewBox="0 0 14 14"><circle cx="7" cy="7" r="5.5" fill="none" stroke="var(--ring)" stroke-width="2"/><path d="M4.5 7l2 2 3-4" fill="none" stroke="var(--ring)" stroke-width="1.6"/></svg><button>Sync Now</button></div>
    </div>
    <div class="body">
      <div class="band"><span class="tab">14 day Rule</span></div>
      <div class="card">
        <div class="period"><div><b>01:17 14-Aug</b><small>Period Start</small></div><div style="text-align:right"><b>01:17 28-Aug</b><small>Period End</small></div></div>
        <div class="range" style="margin-top:8px"><span>Work Completed</span><span>144 hr</span></div>
        <div class="progress"><i></i></div>
        <div class="range"><span>0 hr</span><span></span></div>
        <div class="grid2">
          <div class="cell"><b>78:08</b><small>Work Completed</small></div>
          <div class="cell"><b>43:01</b><small>Maximum Continuous Rest</small></div>
          <div class="cell"><b>65:52</b><small>Work Remaining</small></div>
          <div class="cell"><b>01:17 27-Aug</b><small>Start 24 hr Rest Before</small></div>
          <div class="cell"><b>62:29</b><small>Period Remaining</small></div>
          <div class="cell"><b>1 / 2</b><small>24 hr Rests Found/Required</small></div>
        </div>
        <div style="text-align:center;padding-top:6px"><b>1/4</b> <small style="color:var(--muted)">Active Periods</small></div>
        <div class="navs"><span class="pill">&lt; Previous</span><span class="pill">Next &gt;</span></div>
      </div>
      <div class="band"><span class="tab">Total Work Since Last 24 hr Rest</span></div>
      <div class="card">
        <div class="progress"><i style="width:40%"></i></div>
        <div class="range"><span>0 hr</span><span>24 hr</span></div>
        <div style="padding-top:6px"><b>02:33 23-Aug</b><br><small style="color:var(--muted)">End of 24 hr Rest</small></div>
      </div>
    </div>
    <nav class="tabbar"><span>⏻<b>Logout</b></span><span>✎<b>Compliance</b></span><span>✉<b>Report transfer</b></span></nav>
  </section>

  <!-- Daily overview -->
  <section class="screen screen--center">
    <div class="status"><span>8:49</span><span>●●● ▢</span></div>
    <div class="header">
      <div class="menu"><i></i><i></i><i></i></div>
      <div class="who"><b>Jack Mercer</b><span>License : 1234567890</span></div>
      <div class="sync"><svg width="14" height="14" viewBox="0 0 14 14"><circle cx="7" cy="7" r="5.5" fill="none" stroke="var(--ring)" stroke-width="2"/><path d="M4.5 7l2 2 3-4" fill="none" stroke="var(--ring)" stroke-width="1.6"/></svg><button>Sync Now</button></div>
    </div>
    <svg width="340" height="180" viewBox="0 0 340 180" role="img" aria-label="Hours worked per day bar chart">
      <g stroke="var(--line)"><line x1="10" y1="15" x2="305" y2="15"/><line x1="10" y1="45" x2="305" y2="45"/><line x1="10" y1="75" x2="305" y2="75"/><line x1="10" y1="105" x2="305" y2="105"/><line x1="10" y1="135" x2="305" y2="135"/><line x1="10" y1="165" x2="305" y2="165"/></g>
      <g fill="var(--muted)" font-size="10" font-family="Lato,sans-serif"><text x="315" y="19">24</text><text x="315" y="49">20</text><text x="315" y="79">16</text><text x="315" y="109">12</text><text x="315" y="139">8</text><text x="315" y="169">4</text></g>
      <rect x="100" y="127" width="9" height="60" rx="4.5" fill="var(--bar-soft)"/>
      <rect x="142" y="104" width="9" height="83" rx="4.5" fill="var(--bar-soft)"/>
      <rect x="183" y="133" width="9" height="54" rx="4.5" fill="var(--bar)"/>
    </svg>
    <div class="days"><span>22</span><span>23</span><span>24</span><span class="on">25</span></div>
    <div class="body">
      <div class="card">
        <span class="date">Fri, 25 Aug 2023</span>
        <div class="grid2">
          <div class="cell"><b>07 : 03</b><small>Total Work</small></div>
          <div class="cell"><b>03 : 46</b><small>Total Rest</small></div>
          <div class="cell"><b>03 : 14</b><small>Night Work</small></div>
          <div class="cell"><b>04 : 46</b><small>Max Night Rest</small></div>
          <div class="cell" style="border-bottom:0"><b>00 : 00</b><small>Long Work</small></div>
          <div class="cell" style="border-bottom:0"><b style="color:var(--alert)">⊗</b><small>Night Rest Break</small></div>
        </div>
      </div>
      <div class="activity">
        <div class="top"><b>Work</b><small>Current Activity</small></div>
        <div class="row"><div><small>Start Date &amp; Time</small><b>25 Aug 2023 - 08:47</b></div><div><small>Duration</small><b>02 : 02</b></div></div>
      </div>
    </div>
    <nav class="tabbar"><span>⏻<b>Logout</b></span><span>✎<b>Compliance</b></span><span>✉<b>Report transfer</b></span><span>↦<b>Return to Shift</b></span></nav>
  </section>

  <!-- Night rests -->
  <section class="screen screen--right">
    <div class="status"><span>8:39</span><span>●●● ▢</span></div>
    <div class="header">
      <div class="menu"><i></i><i></i><i></i></div>
      <div class="who"><b>Jack Mercer</b><span>License : 1234567890</span></div>
      <div class="sync"><svg width="14" height="14" viewBox="0 0 14 14"><circle cx="7" cy="7" r="5.5" fill="none" stroke="var(--ring)" stroke-width="2"/><path d="M4.5 7l2 2 3-4" fill="none" stroke="var(--ring)" stroke-width="1.6"/></svg><button>Sync Now</button></div>
    </div>
    <div class="body">
      <div class="card">
        <div class="grid2">
          <div class="cell"><b>17:25</b><small>Night Work</small></div>
          <div class="cell"><b>17:25</b><small>Total Night Long Work</small></div>
          <div class="cell" style="border-bottom:0"><b>1/4</b><small>Active Periods</small></div>
          <div class="cell" style="border-bottom:0"><b>00:00</b><small>Long Work</small></div>
        </div>
        <div class="navs"><span class="pill">&lt; Previous</span><span class="pill">Next &gt;</span></div>
      </div>
      <div class="band"><span class="tab">Night Rests</span></div>
      <div class="card">
        <div class="period"><div><b>17 Aug</b><small>Period Start</small></div><div style="text-align:right"><b>30 Aug</b><small>Period End</small></div></div>
        <div class="grid2">
          <div class="cell" style="border-bottom:0"><b>01:00 29-Aug</b><small>Start Next Night Rest Before</small></div>
          <div class="cell" style="border-bottom:0"><b>1</b><small>Consecutive Night Rests Required</small></div>
        </div>
        <div class="cal">
          <span>12</span><span>13</span><span class="x">14</span><span class="x">15</span><span>16</span><span class="x">17</span><span>18</span>
          <span class="x">19</span><span class="x">20</span><span class="x">21</span><span>22</span><span class="x">23</span><span class="x">24</span><span class="on">25</span>
        </div>
        <div class="navs"><span class="pill">&lt; Previous</span><span class="pill">Next &gt;</span></div>
      </div>
      <div class="band"><span class="tab">24 Hour Continuous Rest</span></div>
      <p class="note">Ticks on calendar indicate dates on which a 24 hour rest break ended. Rest is 24 continuous hours stationary rest time taken after no more than the allowed work.</p>
    </div>
    <nav class="tabbar"><span>✎<b>Compliance</b></span><span>✉<b>Report transfer</b></span><span>↦<b>Start Shift</b></span></nav>
  </section>
</div>
</body>
</html>
```